Book Cover: Quiet Harbor: Small Ceremonies For The Restless Soul

I would like a full cover spread- front, back and spine as well as a stand alone front cover for Kindle for the book. Design a cover that mirrors the profound depth and dynamic energy of 'Quiet Harbor.' Envision a visual tapestry that draws readers into a transformative journey, where spirituality and self-care unite. Explore vibrant colors, intricate textures, and a sense of inner radiance that beckons readers to explore the book's rich wisdom within. See images for design inspiration attached. Even though some of the images are cartoon, I'd like the cover to be more serious than playful and very elegant.

About this book (back cover copy)
Are you ready to embark on a transformative journey and elevate your daily existence? "Quiet Harbor" is a treasure trove of practical yet profound rituals and wisdom from renowned self-care, healing, and spirituality experts.

Within these pages, you'll uncover a tapestry of guidance and insight from some of the world's most respected mentors. Their collective wisdom is your key to creating a sacred sanctuary within your everyday life.

From invigorating morning rituals to meditative practices, empowering affirmations, and transformative energy healing, you'll find a rich tapestry of tools to nurture a deeper connection with yourself and the universe.

Whether you're a seasoned practitioner or a newcomer to the world of self-care and spirituality, "Quiet Harbor" is your trusted companion on the journey to transform your life and elevate your daily experience. Open this book today and start your sacred, fulfilling adventure.

Colors
0094D4
00A9DD
6FCCEA
C7EBF8
E9F6FB
E54698
E96AAD
F1A4CE
F9D9EA
FCEFF6
6B429C
8869AF
B7A5CE
E3DAEB
F3F0F8

Requirements
Must have
• Title: Quiet Harbor: Subtitle: Small Ceremonies For The Restless Soul Name of Publisher: Lantern Bough Publishing- Logo on the back Back cover copy

```html
<!DOCTYPE html>
<html lang="en">
<head>
<meta charset="utf-8">
<title>Quiet Harbor — Cover Spread</title>
<link rel="stylesheet" href="https://fonts.googleapis.com/css2?family=Allura&family=Arimo:ital,wght@0,400;0,700;1,400&display=swap">
<style>
  :root {
    --stage: #1e1e1e;
    --paper: #ffffff;
    --ink: #1a1a1a;
    --pink: #e54698;
    --pink-soft: #f1a4ce;
    --pink-pale: #f9d9ea;
    --violet: #6b429c;
    --violet-soft: #8869af;
    --gold-light: #f6d77c;
    --gold-mid: #d4ae55;
    --gold-deep: #a07d2c;
  }
  * { margin: 0; padding: 0; box-sizing: border-box; }
  html, body { width: 1200px; height: 1200px; overflow: hidden; }
  body { background: var(--stage); font-family: "Arimo", Arial, sans-serif; color: var(--ink); }

  .spread {
    position: absolute; left: 40px; top: 202px;
    width: 1120px; height: 795px;
    background: var(--paper);
    display: flex;
  }

  /* Back cover */
  .back-cover { position: relative; width: 530px; height: 100%; }
  .back-title { position: absolute; left: 120px; top: 40px; }
  .back-subtitle {
    position: absolute; left: 0; right: 0; top: 172px;
    text-align: center; font-size: 21px; white-space: nowrap;
  }
  .script-accent {
    font-family: "Allura", cursive; color: var(--pink);
    font-size: 44px; line-height: 0; vertical-align: -4px; margin-left: 4px;
  }
  .back-copy {
    position: absolute; left: 45px; width: 440px; top: 245px;
    text-align: center; font-size: 14.2px; line-height: 21px;
  }
  .back-copy p + p { margin-top: 20px; }
  .back-copy strong { font-weight: 700; }
  .publisher-mark {
    position: absolute; left: 52px; top: 712px;
    font-size: 22px; font-weight: 400; color: var(--ink); letter-spacing: 1px;
    line-height: 32px; text-align: center;
  }

  /* Spine */
  .spine {
    position: relative; width: 60px; height: 100%;
    display: flex; justify-content: center; padding-top: 28px;
  }
  .spine-text {
    writing-mode: vertical-rl; white-space: nowrap;
    font-size: 15px; display: flex; align-items: center; gap: 14px;
  }
  .spine-title {
    font-family: "Allura", cursive; font-size: 52px; line-height: 1;
    color: var(--gold-mid);
  }
  .spine-subtitle .script-accent { font-size: 30px; vertical-align: 0; }
  .spine-publisher { font-size: 16px; }
  .spine-publisher b { font-weight: 700; }

  /* Front cover */
  .front-cover { position: relative; width: 530px; height: 100%; overflow: hidden; }
  .front-art {
    position: absolute; right: 0; top: 0; width: 530px; height: 795px;
  }
  .front-title { position: absolute; left: 0; top: 10px; }
  .front-subtitle {
    position: absolute; left: 32px; top: 628px;
    font-size: 21px; line-height: 30px;
  }
  .front-subtitle .line-2 { padding-left: 50px; }
  .front-subtitle .script-accent { font-size: 52px; }
  .front-publisher { position: absolute; left: 32px; top: 740px; font-size: 22px; }
  .front-publisher b { font-weight: 700; }
</style>
</head>
<body>
  <div class="spread">

    <section class="back-cover">
      <svg class="back-title" width="300" height="130" viewBox="0 0 300 130" aria-label="Quiet Harbor">
        <defs>
          <linearGradient id="goldBack" x1="0" y1="0" x2="1" y2="1">
            <stop offset="0" stop-color="#f6d77c"/>
            <stop offset="0.55" stop-color="#d4ae55"/>
            <stop offset="1" stop-color="#a07d2c"/>
          </linearGradient>
        </defs>
        <text x="20" y="72" font-family="Allura, cursive" font-size="92" fill="url(#goldBack)">Quiet</text>
        <text x="70" y="122" font-family="Allura, cursive" font-size="66" fill="url(#goldBack)">Harbor</text>
      </svg>

      <p class="back-subtitle">Small Ceremonies For The Restless<span class="script-accent">Soul</span></p>

      <div class="back-copy">
        <p><strong>Are you ready to embark on a transformative journey and elevate your daily existence?</strong> <em>"Quiet Harbor"</em> is a treasure trove of practical yet profound rituals and wisdom from renowned self-care, healing, and spirituality experts.</p>
        <p>Within these pages, you'll uncover a tapestry of guidance and insight from some of the world's most respected mentors. Their collective wisdom is your key to creating a sacred sanctuary within your everyday life.</p>
        <p>From invigorating morning rituals to meditative practices, empowering affirmations, and transformative energy healing, you'll find a rich tapestry of tools to nurture a deeper connection with yourself and the universe.</p>
        <p>Whether you're a seasoned practitioner or a newcomer to the world of self-care and spirituality, "Quiet Harbor" is your trusted companion on the journey to transform your life and elevate your daily experience. Open this book today and start your sacred, fulfilling adventure.</p>
      </div>

      <div class="publisher-mark">Lantern Bough<br>Publishing</div>
    </section>

    <section class="spine">
      <div class="spine-text">
        <span class="spine-title">Quiet Harbor</span>
        <span class="spine-subtitle">Small Ceremonies For The Restless<span class="script-accent">Soul</span></span>
        <span class="spine-publisher"><b>Lantern Bough</b> Publishing</span>
      </div>
    </section>

    <section class="front-cover">
      <svg class="front-art" viewBox="0 0 530 795" role="img" aria-label="Illustration of layered profile silhouettes in pink and violet tones">
        <defs>
          <linearGradient id="artFill" x1="0" y1="0" x2="1" y2="1">
            <stop offset="0" stop-color="#f9d9ea"/>
            <stop offset="0.35" stop-color="#e96aad"/>
            <stop offset="0.65" stop-color="#e54698"/>
            <stop offset="1" stop-color="#6b429c"/>
          </linearGradient>
          <linearGradient id="artFade" x1="0" y1="0" x2="1" y2="0">
            <stop offset="0" stop-color="#fff" stop-opacity="0"/>
            <stop offset="0.35" stop-color="#fff" stop-opacity="1"/>
          </linearGradient>
          <mask id="artMask">
            <rect width="530" height="795" fill="url(#artFade)"/>
          </mask>
        </defs>
        <path d="M530 240 C430 245 360 320 340 420 C325 500 250 560 300 640 C330 700 270 760 280 795 L530 795 Z"
              fill="url(#artFill)" mask="url(#artMask)" opacity="0.92"/>
      </svg>

      <svg class="front-title" width="530" height="320" viewBox="0 0 530 320" aria-label="Quiet Harbor">
        <defs>
          <linearGradient id="goldFront" x1="0" y1="0" x2="1" y2="1">
            <stop offset="0" stop-color="#f6d77c"/>
            <stop offset="0.55" stop-color="#d4ae55"/>
            <stop offset="1" stop-color="#a07d2c"/>
          </linearGradient>
        </defs>
        <text x="10" y="185" font-family="Allura, cursive" font-size="240" fill="url(#goldFront)">Quiet</text>
        <text x="120" y="290" font-family="Allura, cursive" font-size="150" fill="url(#goldFront)">Harbor</text>
      </svg>

      <p class="front-subtitle">
        Small Ceremonies For<br>
        <span class="line-2">The Restless<span class="script-accent">Soul</span></span>
      </p>
      <p class="front-publisher"><b>Lantern Bough</b> Publishing</p>
    </section>

  </div>
</body>
</html>
```